Cyber Security Site Design (Products & Consulting)

I need my website redesigned to be engaging, clean, efficient and modern. My company (when its up and running) is going to be concentrated on two things: a few specific products for cyber security as well as cyber security consulting services. The background I bring to the field is having worked with small companies all the way to the largest government organizations and advising them on their security posture and how to improve it. We need the ability to add products and services easily.

For a sample product, you can use either Tarnet (http://www.tarnet-relay.org/) or Verodyne Ashmantle (https://www.verodyne.com/products/relay-hx-and-fortified-edge-portal).

It will replace https://lumerafieldworks.com/

Target Market(s)

Cyber Security professionals in all verticals

Coding

Coded - Design and coding required

Number of Pages Required

4 page

Font styles to use
Sans Serif

Colors
6b449b

Requirements
Must have
• Ability to easily modify
• Have main page
• Have product specific pages
• Have consulting services pages
• Have executive team information
• Clean, modern design
• Usage of the logo and its color scheme
Nice to have
• I like the idea of a left collapsed sidebar (so icons only) that can expand for text.
• I am also open to a very unique landing page, possibly a shape in the middle (hexagons maybe?) with each of the options there.
Should not have
• Nothing that looks like it came out of a hacker movie

```html
<!DOCTYPE html>
<html lang="en">
<head>
<meta charset="utf-8">
<title>Lumera Fieldworks – Services</title>
<link href="https://fonts.googleapis.com/css2?family=Montserrat:wght@400;500&family=Roboto:wght@400;500;700&family=Signika:wght@300;400;600&display=swap" rel="stylesheet">
<style>
:root{
  --brand:#6b449b;
  --footer:#653a97;
  --footer-bar:#57307f;
  --ink:#1f1f24;
  --body:#4a4a50;
  --card:#f3f3f3;
  --line:#d8d8dc;
  --white:#ffffff;
}
*{margin:0;padding:0;box-sizing:border-box}
html,body{width:1200px;height:2461px;overflow:hidden;background:var(--white)}
body{position:relative;font-family:"Montserrat",sans-serif;color:var(--body)}

/* header */
.site-header{position:absolute;left:0;top:0;width:1200px;height:70px;background:var(--white);border-bottom:1px solid #e6e6ea}
.brand{position:absolute;left:141px;top:12px;display:flex;align-items:center;gap:8px}
.brand-dot{width:36px;height:36px;border-radius:50%;background:var(--brand)}
.brand-name{font-family:"Roboto",sans-serif;font-weight:500;font-size:22px;color:var(--brand);letter-spacing:.5px;line-height:1}
.brand-name small{display:block;font-size:9px;letter-spacing:6px;margin-top:3px}
.main-nav{position:absolute;top:30px;left:453px;display:flex;gap:34px;font-family:"Roboto",sans-serif;font-size:13px;color:#222}
.main-nav .active{color:var(--brand)}
.btn{display:inline-flex;align-items:center;gap:10px;background:var(--brand);color:var(--white);font-family:"Roboto",sans-serif;font-size:13px;border-radius:18px;box-shadow:0 4px 10px rgba(107,68,155,.35)}
.btn .ring{width:18px;height:18px;border-radius:50%;border:2.5px solid var(--white)}
.header-cta{position:absolute;left:926px;top:19px;height:31px;padding:0 12px}

/* hero */
.hero{position:absolute;left:0;top:70px;width:1200px;height:373px}
.hero-art{position:absolute;inset:0}
.hero-title{position:absolute;left:0;width:1200px;top:117px;text-align:center;font-family:"Signika",sans-serif;font-weight:600;font-size:45px;color:var(--white);text-shadow:0 2px 6px rgba(0,0,0,.35)}
.hero-sub{position:absolute;left:0;width:1200px;top:172px;text-align:center;font-family:"Signika",sans-serif;font-size:18px;color:var(--white);text-shadow:0 1px 4px rgba(0,0,0,.45)}
.hero-cta{position:absolute;left:512px;top:225px;height:31px;padding:0 14px 0 10px}

.breadcrumb{position:absolute;left:141px;top:431px;font-family:"Roboto",sans-serif;font-size:13px;color:#222}
.breadcrumb span{margin:0 10px}
.breadcrumb .current{color:var(--brand);margin:0}

/* services */
.section-title{position:absolute;left:0;width:1200px;top:512px;text-align:center;font-family:"Signika",sans-serif;font-size:41px;color:var(--ink);font-weight:400}
.section-title b{font-weight:600}
.title-rule{position:absolute;left:466px;top:578px;width:269px;height:1px;background:var(--line)}
.title-rule::after{content:"";position:absolute;left:114px;top:-2px;width:42px;height:4px;background:var(--brand)}

.service{position:absolute;left:200px;width:858px;height:201px;background:var(--card)}
.service-icon{position:absolute;left:-57px;top:42px;width:114px;height:114px;border-radius:50%;background:var(--brand);border:4px solid var(--white);box-shadow:0 0 0 1px #ececec;display:flex;align-items:center;justify-content:center}
.service h3{position:absolute;left:86px;top:20px;font-family:"Signika",sans-serif;font-weight:400;font-size:21px;color:var(--ink)}
.service p{position:absolute;left:86px;top:58px;width:748px;font-size:12.9px;line-height:23px;color:var(--body)}

/* footer */
.site-footer{position:absolute;left:0;top:1868px;width:1200px;height:593px}
.footer-shape{position:absolute;inset:0}
.footer-brand{position:absolute;left:497px;top:33px;display:flex;align-items:center;gap:9px}
.footer-brand .brand-dot{background:var(--white);width:40px;height:40px}
.footer-brand .brand-name{color:var(--white);font-size:28px}
.footer-brand .brand-name small{font-size:10px;letter-spacing:8px}
.footer-rule{position:absolute;left:0;top:112px;width:1200px;height:1px;background:rgba(255,255,255,.15)}
.cta-title{position:absolute;left:137px;top:158px;font-family:"Signika",sans-serif;font-weight:300;font-size:36px;color:var(--white);letter-spacing:1px}
.cta-title b{font-weight:600}
.cta-text{position:absolute;left:141px;top:210px;width:360px;font-family:"Roboto",sans-serif;font-size:14px;line-height:17px;color:var(--white)}
.col-head{position:absolute;font-family:"Roboto",sans-serif;font-weight:400;font-size:16px;color:var(--white)}
.col-head::after{content:"";position:absolute;left:0;top:28px;width:44px;height:1px;background:rgba(255,255,255,.6)}
.contact-list{position:absolute;left:138px;top:340px;font-family:"Roboto",sans-serif;color:var(--white)}
.contact-row{display:flex;gap:12px;align-items:flex-start;margin-bottom:8px}
.contact-row svg{flex:none;margin-top:2px}
.contact-org{font-size:12.5px;font-weight:500}
.contact-addr{font-size:11px;line-height:17px}
.contact-phone{font-size:16px;font-weight:700}
.contact-mail{font-size:11px}
.quick-links{position:absolute;left:400px;top:338px;list-style:none;font-family:"Roboto",sans-serif;font-size:11px;color:var(--white)}
.quick-links li{height:19.3px}
.quick-links li::before{content:"›";margin-right:10px}
.form-panel{position:absolute;left:614px;top:158px;width:444px;height:386px;background:var(--white)}
.field{position:absolute;left:35px;width:374px;height:38px;border:1px solid #cfcfd4;font-family:"Roboto",sans-serif;font-size:12px;color:#6a6a70;padding:11px 15px}
.field.message{height:58px}
.form-submit{position:absolute;left:35px;top:322px;height:31px;padding:0 16px 0 10px}
.footer-bar{position:absolute;left:0;top:544px;width:1200px;height:49px;background:var(--footer-bar)}
.copyright{position:absolute;left:141px;top:18px;font-family:"Roboto",sans-serif;font-size:11px;color:var(--white)}
.socials{position:absolute;left:781px;top:10px;display:flex;gap:7px}
.socials span{width:29px;height:29px;border-radius:50%;border:1.5px solid var(--white)}
</style>
</head>
<body>

<header class="site-header">
  <div class="brand"><span class="brand-dot"></span><span class="brand-name">LUMERA<small>FIELDWORKS</small></span></div>
  <nav class="main-nav">
    <span>HOME</span><span>ABOUT</span><span>OUR TEAM</span><span>OUR PRODUCTS</span><span class="active">SERVICES</span>
  </nav>
  <span class="btn header-cta"><span class="ring"></span>CONTACT US</span>
</header>

<section class="hero">
  <svg class="hero-art" width="1200" height="373" viewBox="0 0 1200 373" role="img" aria-label="City skyline at dusk photograph">
    <defs>
      <linearGradient id="sky" x1="0" y1="0" x2="0" y2="1">
        <stop offset="0" stop-color="#5f6e86"/>
        <stop offset=".35" stop-color="#8a8fa0"/>
        <stop offset=".6" stop-color="#6b5a57"/>
        <stop offset="1" stop-color="#5b3f35"/>
      </linearGradient>
    </defs>
    <polygon points="0,0 1200,0 1200,257 600,373 0,257" fill="url(#sky)"/>
  </svg>
  <h1 class="hero-title">CYBER SECURITY CONSULTING &amp; PRODUCTS</h1>
  <p class="hero-sub">A full range of Cyber Security Consulting Services and Products to meet your business requirements</p>
  <span class="btn hero-cta"><span class="ring"></span>GET STARTED NOW!</span>
</section>

<div class="breadcrumb">HOME<span>»</span><span class="current">SERVICES</span></div>

<h2 class="section-title">OUR <b>SERVICES</b></h2>
<div class="title-rule"></div>

<article class="service" style="top:612px">
  <div class="service-icon">
    <svg width="58" height="50" viewBox="0 0 58 50" fill="none" stroke="#fff" stroke-width="2.5">
      <rect x="2" y="2" width="54" height="40" rx="2"/><line x1="2" y1="11" x2="56" y2="11"/>
      <line x1="10" y1="22" x2="48" y2="22"/><circle cx="12" cy="22" r="2"/><circle cx="46" cy="22" r="2"/>
      <rect x="22" y="30" width="14" height="12"/><path d="M25 30v-4a4 4 0 0 1 8 0v4"/>
    </svg>
  </div>
  <h3>Cyber Security Services</h3>
  <p>Lorem ipsum dolor sit amet, consectetur adipiscing elit, sed do eiusmod tempor incididunt ut labore et dolore magna aliqua.Sed ut perspiciatis unde omnis iste natus error sit voluptatem accusantium doloremque laudantium, totam rem aperiam, eaque ipsa quae ab illo inventore veritatis et quasi architecto beatae vitae dicta sunt explicabo. Nemo enim ipsam voluptatem quia voluptas sit aspernatur aut odit aut fugit, sed quia consequuntur magni dolores eos qui ratione voluptatem sequi nesciunt.</p>
</article>

<article class="service" style="top:856px">
  <div class="service-icon">
    <svg width="46" height="56" viewBox="0 0 46 56" fill="none" stroke="#fff" stroke-width="2.5">
      <path d="M2 2h32l10 10v42H2z"/><line x1="10" y1="46" x2="36" y2="46"/>
      <circle cx="23" cy="22" r="6"/><path d="M15 16l4 3M31 16l-4 3M14 22h3M29 22h3M15 29l4-3M31 29l-4-3M23 14v-3"/>
    </svg>
  </div>
  <h3>Managed Security Services</h3>
  <p>Lorem ipsum dolor sit amet, consectetur adipiscing elit, sed do eiusmod tempor incididunt ut labore et dolore magna aliqua.Sed ut perspiciatis unde omnis iste natus error sit voluptatem accusantium doloremque laudantium, totam rem aperiam, eaque ipsa quae ab illo inventore veritatis et quasi architecto beatae vitae dicta sunt explicabo. Nemo enim ipsam voluptatem quia voluptas sit aspernatur aut odit aut fugit, sed quia consequuntur magni dolores eos qui ratione voluptatem sequi nesciunt.</p>
</article>

<article class="service" style="top:1100px">
  <div class="service-icon">
    <svg width="60" height="56" viewBox="0 0 60 56" fill="none" stroke="#fff" stroke-width="2.5">
      <path d="M29 6c-4-6-14-4-14 3-7 0-11 8-7 13-5 4-4 13 2 15 0 7 7 12 14 9 2 3 5 3 5 0z"/>
      <path d="M31 6c4-6 14-4 14 3 7 0 11 8 7 13 5 4 4 13-2 15 0 7-7 12-14 9-2 3-5 3-5 0z"/>
      <path d="M20 20h6M18 32h8M36 18v8M40 34h-6"/>
    </svg>
  </div>
  <h3>Deep Slight Intelligence</h3>
  <p>Lorem ipsum dolor sit amet, consectetur adipiscing elit, sed do eiusmod tempor incididunt ut labore et dolore magna aliqua.Sed ut perspiciatis unde omnis iste natus error sit voluptatem accusantium doloremque laudantium, totam rem aperiam, eaque ipsa quae ab illo inventore veritatis et quasi architecto beatae vitae dicta sunt explicabo. Nemo enim ipsam voluptatem quia voluptas sit aspernatur aut odit aut fugit, sed quia consequuntur magni dolores eos qui ratione voluptatem sequi nesciunt.</p>
</article>

<article class="service" style="top:1344px">
  <div class="service-icon">
    <svg width="62" height="60" viewBox="0 0 62 60" fill="none" stroke="#fff" stroke-width="2.5">
      <path d="M31 2v30M25 8l6-6 6 6M8 16v40M3 21l5-5 5 5M54 16v40M49 21l5-5 5 5"/>
      <path d="M18 56v-8a13 13 0 0 1 26 0v8M2 56h58"/><path d="M14 44l6-4M48 44l-6-4"/>
    </svg>
  </div>
  <h3>Incident Response Services</h3>
  <p>Lorem ipsum dolor sit amet, consectetur adipiscing elit, sed do eiusmod tempor incididunt ut labore et dolore magna aliqua.Sed ut perspiciatis unde omnis iste natus error sit voluptatem accusantium doloremque laudantium, totam rem aperiam, eaque ipsa quae ab illo inventore veritatis et quasi architecto beatae vitae dicta sunt explicabo. Nemo enim ipsam voluptatem quia voluptas sit aspernatur aut odit aut fugit, sed quia consequuntur magni dolores eos qui ratione voluptatem sequi nesciunt.</p>
</article>

<article class="service" style="top:1588px">
  <div class="service-icon">
    <svg width="56" height="56" viewBox="0 0 56 56" fill="none" stroke="#fff" stroke-width="2.5">
      <path d="M4 12a10 10 0 0 0 14 10l30 30 5-5-30-30A10 10 0 0 0 13 3l6 6-2 6-6 2z"/>
      <path d="M52 6l-6-2-18 18 5 5 18-18zM24 32L8 48l4 4 16-16"/>
    </svg>
  </div>
  <h3>Other Services</h3>
  <p>Lorem ipsum dolor sit amet, consectetur adipiscing elit, sed do eiusmod tempor incididunt ut labore et dolore magna aliqua.Sed ut perspiciatis unde omnis iste natus error sit voluptatem accusantium doloremque laudantium, totam rem aperiam, eaque ipsa quae ab illo inventore veritatis et quasi architecto beatae vitae dicta sunt explicabo. Nemo enim ipsam voluptatem quia voluptas sit aspernatur aut odit aut fugit, sed quia consequuntur magni dolores eos qui ratione voluptatem sequi nesciunt.</p>
</article>

<footer class="site-footer">
  <svg class="footer-shape" width="1200" height="593" viewBox="0 0 1200 593" aria-hidden="true">
    <polygon points="0,42 600,0 1200,42 1200,593 0,593" fill="#653a97"/>
  </svg>
  <div class="footer-brand"><span class="brand-dot"></span><span class="brand-name">LUMERA<small>FIELDWORKS</small></span></div>
  <div class="footer-rule"></div>

  <h2 class="cta-title"><b>LET'S</b> GET STARTED</h2>
  <p class="cta-text">Take the first step to growing your business with a FREE consultation and quote.</p>

  <h4 class="col-head" style="left:138px;top:296px">Contact Details</h4>
  <h4 class="col-head" style="left:400px;top:294px">Quick Links</h4>

  <div class="contact-list">
    <div class="contact-row">
      <svg width="10" height="14" viewBox="0 0 10 14"><path d="M5 0a5 5 0 0 1 5 5c0 4-5 9-5 9S0 9 0 5a5 5 0 0 1 5-5z" fill="#fff"/><circle cx="5" cy="5" r="2" fill="#653a97"/></svg>
      <div><div class="contact-org">LUMERA CYBER SECURITY</div><div class="contact-addr">4810 Alder Ridge Rd, Suite<br>#210 Brookfield, TX 77990</div></div>
    </div>
    <div class="contact-row">
      <svg width="12" height="12" viewBox="0 0 12 12"><path d="M2 0l3 3-1.5 2a7 7 0 0 0 3.5 3.5L9 7l3 3-2 2C5 12 0 7 0 2z" fill="#fff"/></svg>
      <div class="contact-phone">555-014-2290</div>
    </div>
    <div class="contact-row" style="margin-top:12px">
      <svg width="12" height="9" viewBox="0 0 12 9"><rect width="12" height="9" fill="#fff"/><path d="M0 0l6 5 6-5" stroke="#653a97" fill="none"/></svg>
      <div class="contact-mail">info@lumeracybersecurity.com</div>
    </div>
  </div>

  <ul class="quick-links">
    <li>Home</li><li>About Us</li><li>Our Team</li><li>Our Products</li><li>Services</li><li>Conatact</li>
  </ul>

  <form class="form-panel">
    <div class="field" style="top:39px">First Name</div>
    <div class="field" style="top:88px">Last Name</div>
    <div class="field" style="top:138px">Email</div>
    <div class="field" style="top:188px">Phone Number</div>
    <div class="field message" style="top:237px">Message</div>
    <span class="btn form-submit"><span class="ring"></span>SUBMIT</span>
  </form>

  <div class="footer-bar">
    <p class="copyright">Copyright © 2018 <b>LumeraCyberSecurity</b>. All Right Reserved.</p>
    <div class="socials"><span></span><span></span><span></span><span></span></div>
  </div>
</footer>

</body>
</html>
```